Moon Tot needs ecommerce website design help

We need someone to set up a fully functional website for us. We sell baby bibs, I attached them along with our company logo (MTG: moon tot goods). The bibs are made of 100% silicon, they are safe, light weight, soft, smooth, flexible, dishwasher safe and has funny faces.

Business name: Moon Tot Goods
Elm Hollow, NY 00000
email: MoonTotGoods@mailbox-example.com
tel.: (555) 014-TOTS
website: MoonTotGoods-example.com

Target Market(s)

18-40

Industry/Entity Type

Baby

Coding

Coded - Design and coding required

Number of Pages Required

5+ page

Requirements
Must have
• 1. Pages: Why buy from us, Contact Us, Home page, Products Page, Blog
• 2. Use the colors from our logo for the web design.
• 3. Need a link that will connect visitors to our facebook, instagram, Pinterest and Tumblr account. Would like links on,the top left side of the page
Nice to have
• My Cart page
• 1. On contact us page, we want to include some type of template for the customer to complete. (Ex: name, email address, contact number, optional home address, comments)
• 2. When clients visit our website, we want a capture/pop up for the customer to subscribe to our email list to receive discounts. (Ex. Want 10% off your next order ? Suscribe to our mailing list below and get a 10% off code to use at check out. If they don't want to subscribe, they have the option to select "No Thank You, I want to pay full price).
• 3. On home page have subscribe to our email list.

```html
<!DOCTYPE html>
<html lang="en">
<head>
<meta charset="utf-8">
<title>Moon Tot Goods – Store</title>
<link href="https://fonts.googleapis.com/css2?family=Open+Sans:wght@300;400;600;700&display=swap" rel="stylesheet">
<style>
:root{
  --blue:#1e9bd7;
  --red:#e8313f;
  --orange:#f0a030;
  --green:#8dc63f;
  --pink:#d4237a;
  --ink:#333;
  --muted:#888;
  --line:#e3e3e3;
  --page:#f4f4f4;
  --footer:#2b2b2b;
  --footer-deep:#1f1f1f;
  --panel:#151515;
}
*{margin:0;padding:0;box-sizing:border-box}
html,body{width:937px;height:1200px;overflow:hidden}
body{font-family:"Open Sans",sans-serif;color:var(--ink);background:#fff;position:relative}
.abs{position:absolute}
.page{position:absolute;inset:0}

/* top bar */
.topbar{left:0;top:0;width:937px;height:47px;background:var(--page);font-size:6.5px;color:var(--muted)}
.topbar span{position:absolute;top:19px}
.topbar .account{color:var(--blue)}
.cart-dot{left:664px;top:16px;width:15px;height:15px;border-radius:50%;background:var(--red)}
.cart-label{left:684px;top:19px;font-size:6.5px;color:var(--blue);font-weight:600}
.cart-label b{color:var(--muted);font-weight:600;margin-left:4px}

/* nav */
.nav{left:0;top:47px;width:937px;height:28px;background:var(--blue)}
.nav a{position:absolute;top:9px;color:#fff;font-size:8px;text-decoration:none}
.brand-card{left:194px;top:44px;width:126px;height:58px;background:#fff;transform:skewY(-4deg);box-shadow:0 2px 4px rgba(0,0,0,.15);display:flex;align-items:center;justify-content:center}
.brand-card span{font-size:22px;font-weight:700;color:var(--green);transform:skewY(4deg)}

/* hero */
.hero{left:0;top:75px;width:937px;height:317px;background:linear-gradient(180deg,#eef3f6,#e2ebef)}
.hero-bib{left:520px;top:20px;width:200px;height:220px;background:radial-gradient(circle at 50% 55%,#d43b93,#9c1a5f 70%,transparent 72%)}
.hero-kicker{left:198px;top:142px;font-size:21px;font-weight:300;color:#444}
.hero-title{left:197px;top:160px;font-size:35px;font-weight:700;color:#222}

/* products */
.section-title{font-size:11px;color:var(--ink)}
.section-title .hl{color:var(--blue)}
.featured .hl{color:var(--red)}
.box{border:1px solid var(--line);background:#fff}
.card-title{font-size:7px;font-weight:700;color:#444}
.card-text{font-size:5.6px;color:var(--muted);line-height:8.8px;width:108px}
.price{font-size:8.8px;color:var(--red)}
.add{font-size:6px;color:var(--muted);display:flex;align-items:center;gap:6px;border:1px solid var(--line);padding:0 6px 0 0;height:14px}
.add i{display:block;width:14px;height:14px;background:var(--orange)}
.bib{border-radius:40% 40% 45% 45%}

/* banners */
.banner{top:870px;width:175px;height:87px;color:#fff;padding:26px 0 0 62px}
.banner b{display:block;font-size:14px;font-weight:400}
.banner small{display:block;font-size:10px;opacity:.8;text-align:right;padding-right:20px}

/* footer */
.footer{left:0;top:984px;width:937px;height:176px;background:var(--footer);color:#999}
.footer h4{position:absolute;top:20px;font-size:8.5px;font-weight:600;color:#ddd}
.footer .small{position:absolute;font-size:6px;color:#888;line-height:9.5px}
.social{width:16px;height:16px;background:#444}
.social.fb{background:var(--blue)}
.pay{width:18px;height:10px;border-radius:2px}
.subbar{left:0;top:1160px;width:937px;height:40px;background:var(--footer-deep);font-size:6.5px;color:#888}
.subbar span{position:absolute;top:15px}

/* overlay + modal */
.dim{position:absolute;inset:0;background:rgba(0,0,0,.74)}
.modal{left:123px;top:195px;width:685px;height:332px;background:var(--panel)}
.modal-photo{left:0;top:0;width:225px;height:332px;background:linear-gradient(160deg,#d6a06b 0%,#9b5a33 40%,#3d9ad6 62%,#2a7bb8 100%)}
.modal-brand{left:453px;top:213px;display:flex;align-items:center;gap:8px;font-size:34px;font-weight:700;color:var(--green)}
.modal-brand i{display:block;width:22px;height:22px;border-radius:50%;background:var(--pink)}
.signup{left:405px;top:289px;width:352px;height:180px;background:#fff;border-radius:2px}
.signup h2{position:absolute;left:45px;top:14px;font-size:20px;font-weight:400;color:#222}
.signup p{position:absolute;left:48px;top:42px;width:295px;font-size:9.3px;line-height:12px;color:#444}
.field{position:absolute;top:90px;width:130px;height:21px;border:1px solid #ccc;font-size:10px;color:#999;padding:3px 8px}
.check{position:absolute;left:51px;top:137px;width:12px;height:12px;border:1px solid #bbb;border-radius:2px}
.check-label{position:absolute;left:71px;top:136px;font-size:8.5px;color:#777}
.subscribe{position:absolute;left:213px;top:130px;width:103px;height:24px;background:var(--red);color:#fff;font-size:13px;display:flex;align-items:center;gap:7px;padding-left:10px}
.subscribe i{display:flex;width:14px;height:14px;border-radius:50%;background:#fff;align-items:center;justify-content:center}
.mail-badge{left:374px;top:310px;width:58px;height:58px;border-radius:50%;background:var(--green);border:3px solid #f2f2f2;display:flex;align-items:center;justify-content:center}
.decline{left:616px;top:485px;font-size:8.8px;color:#fff;text-decoration:underline}
</style>
</head>
<body>
<div class="page">
  <div class="abs topbar">
    <span style="left:197px">English ▾</span>
    <span style="left:249px">US Dollar ▾</span>
    <span style="left:402px">Default welcome msg!</span>
    <span class="account" style="left:482px">My account</span>
    <span style="left:530px">My Wishlist</span>
    <span style="left:577px">Checkout</span>
    <span style="left:618px">Log in</span>
  </div>
  <div class="abs cart-dot"></div>
  <div class="abs cart-label">MY CART<b>0 items</b></div>

  <div class="abs nav">
    <svg class="abs" style="left:440px;top:8px" width="11" height="11" viewBox="0 0 12 12"><path d="M1 6 6 1l5 5H9.5v5h-2.5V8h-2v3H2.5V6z" fill="#fff"/></svg>
    <a style="left:472px">Products</a>
    <a style="left:533px">Why buy from us</a>
    <a style="left:626px">Blog</a>
    <a style="left:668px">Contact us</a>
    <svg class="abs" style="left:725px;top:7px" width="13" height="13" viewBox="0 0 14 14"><circle cx="7" cy="7" r="6" fill="none" stroke="#fff"/><circle cx="6.3" cy="6.3" r="2.3" fill="none" stroke="#fff"/><path d="M8 8l2 2" stroke="#fff"/></svg>
  </div>
  <div class="abs brand-card"><span>MTG</span></div>

  <div class="abs hero">
    <div class="abs hero-bib bib" role="img" aria-label="Magenta silicone bib product photo"></div>
  </div>
  <div class="abs hero-kicker">MAURIS SED 2016</div>
  <div class="abs hero-title">DONEC</div>

  <!-- new arrivals -->
  <div class="abs section-title" style="left:204px;top:528px"><span class="hl">New</span> Arrivals</div>
  <div class="abs box" style="left:194px;top:548px;width:134px;height:224px"></div>
  <div class="abs box" style="left:328px;top:548px;width:134px;height:224px;border:2px solid var(--red)"></div>
  <div class="abs bib" style="left:218px;top:568px;width:82px;height:92px;background:#2a8fd1" role="img" aria-label="Blue shark bib"></div>
  <div class="abs bib" style="left:352px;top:568px;width:82px;height:92px;background:#f2a623" role="img" aria-label="Orange tiger bib"></div>
  <div class="abs card-title" style="left:205px;top:675px">Morbi neque feugiat nec</div>
  <div class="abs card-text" style="left:205px;top:688px">Lorem ipsum dolor sit amet consect etur adipiscing elit tincidunt sceleris que lectus a scelerisque.</div>
  <div class="abs price" style="left:205px;top:720px">$ 35.00</div>
  <div class="abs add" style="left:205px;top:741px"><i></i>Add to cart</div>
  <div class="abs card-title" style="left:339px;top:675px">Morbi neque quis feugiat nec</div>
  <div class="abs card-text" style="left:339px;top:688px">Lorem ipsum dolor sit amet consect etur adipiscing elit tincidunt sceleris que lectus a scelerisque.</div>
  <div class="abs price" style="left:339px;top:720px">$ 54.00</div>
  <div class="abs add" style="left:339px;top:741px"><i style="background:var(--red)"></i>Add to cart</div>

  <!-- featured -->
  <div class="abs section-title featured" style="left:486px;top:528px"><span class="hl">Featured</span> Products</div>
  <div class="abs box" style="left:475px;top:554px;width:268px;height:106px"></div>
  <div class="abs box" style="left:475px;top:663px;width:268px;height:109px"></div>
  <div class="abs bib" style="left:494px;top:562px;width:72px;height:84px;background:#6cb33f" role="img" aria-label="Green frog bib"></div>
  <div class="abs bib" style="left:494px;top:672px;width:72px;height:86px;background:#d9e03a" role="img" aria-label="Yellow bib"></div>
  <div class="abs card-title" style="left:616px;top:562px">Morbi neque quis feugiat nec</div>
  <div class="abs card-text" style="left:616px;top:574px">Lorem ipsum dolor sit amet consect etur adipiscing elit tincidunt sceleris que lectus a scelerisque.</div>
  <div class="abs price" style="left:616px;top:607px">$ 25.00</div>
  <div class="abs add" style="left:616px;top:628px"><i></i>Add to cart</div>
  <div class="abs card-title" style="left:616px;top:671px">Morbi neque quis feugiat nec</div>
  <div class="abs card-text" style="left:616px;top:683px">Lorem ipsum dolor sit amet consect etur adipiscing elit tincidunt sceleris que lectus a scelerisque.</div>
  <div class="abs price" style="left:616px;top:716px">$ 52.00</div>
  <div class="abs add" style="left:616px;top:738px"><i></i>Add to cart</div>

  <!-- banners -->
  <div class="abs banner" style="left:194px;background:var(--red)"><b>NEW AMAZING</b><small>Spring collection</small></div>
  <div class="abs banner" style="left:381px;background:var(--orange)"><b>DISHWASHER</b><small>SAFE</small></div>
  <div class="abs banner" style="left:568px;background:var(--green)"><b>SMOOTH</b><small>Lorem ipsum dolor</small></div>

  <!-- footer -->
  <div class="abs footer">
    <h4 style="left:194px">Socialize</h4>
    <h4 style="left:294px">Useful links</h4>
    <h4 style="left:440px">Contact</h4>
    <h4 style="left:614px">Newsletter</h4>
    <div class="abs social fb" style="left:194px;top:48px"></div>
    <div class="abs social" style="left:194px;top:66px"></div>
    <div class="abs social" style="left:194px;top:84px"></div>
    <div class="abs social" style="left:194px;top:102px"></div>
    <div class="small" style="left:294px;top:46px;line-height:17.6px">› Dolor sit amet<br>› Nam cursus nunc<br>› Fermentum<br>› Consequat<br>› Morbi mauris<br>› Praesent felis<br>› Molestie nec nibh</div>
    <svg class="abs" style="left:438px;top:48px" width="7" height="9" viewBox="0 0 8 10"><path d="M4 0a3.5 3.5 0 0 0-3.5 3.5C.5 6 4 10 4 10s3.5-4 3.5-6.5A3.5 3.5 0 0 0 4 0z" fill="#999"/></svg>
    <div class="small" style="left:453px;top:46px">Moon Tot Goods<br>Elm Hollow, NY 00000</div>
    <svg class="abs" style="left:437px;top:77px" width="9" height="7" viewBox="0 0 9 7"><rect width="9" height="7" fill="#999"/><path d="M0 0l4.5 4L9 0" stroke="#2b2b2b" fill="none"/></svg>
    <div class="small" style="left:453px;top:74px">email: MoonTotGoods@mailbox-example.com</div>
    <svg class="abs" style="left:437px;top:94px" width="9" height="9" viewBox="0 0 10 10"><path d="M2 0l2 2.5-1.2 1.5a6 6 0 0 0 3.2 3.2L7.5 6 10 8l-1.5 2C4 10 0 6 0 1.5z" fill="#999"/></svg>
    <div class="small" style="left:453px;top:92px">tel.: (555) 014-TOTS</div>
    <div class="small" style="left:614px;top:46px;color:#bbb;font-weight:600">Sign Up for Our Newsletter:</div>
    <div class="small" style="left:614px;top:59px;width:130px">Get the word out Share this page with your friends and family. Enter your email address...</div>
    <div class="abs" style="left:614px;top:94px;width:112px;height:18px;background:#f4f4f4"></div>
    <div class="abs" style="left:726px;top:94px;width:18px;height:18px;background:var(--red)"></div>
    <div class="abs pay" style="left:616px;top:122px;background:#e07b30"></div>
    <div class="abs pay" style="left:637px;top:122px;background:#3a5fa8"></div>
    <div class="abs pay" style="left:658px;top:122px;background:#c9463d"></div>
    <div class="abs pay" style="left:679px;top:122px;background:#3c8ac4"></div>
  </div>
  <div class="abs subbar">
    <span style="left:194px">About Us</span>
    <span style="left:234px">Privacy Policy</span>
    <span style="left:290px">Search Terms</span>
    <span style="left:345px">Advanced Search</span>
    <span style="left:412px">Contact Us</span>
    <span style="left:609px">Copyright © 2016 <b style="color:var(--orange);font-weight:400">Yoursite</b> All reversed.</span>
  </div>
</div>

<div class="dim"></div>

<div class="abs modal">
  <div class="abs modal-photo" role="img" aria-label="Photo of a smiling baby wearing a blue silicone bib"></div>
</div>
<div class="abs modal-brand"><i></i>MTG</div>

<div class="abs signup">
  <h2>Subscribe to our newsletter</h2>
  <p>Want 10% off your next order ? Suscribe to our mailing list below and get a 10% off code to use at check out</p>
  <div class="field" style="left:48px">Name</div>
  <div class="field" style="left:188px">email address</div>
  <div class="check"><svg width="10" height="10" viewBox="0 0 10 10"><path d="M2 5l2 2 4-4.5" stroke="#999" fill="none" stroke-width="1.2"/></svg></div>
  <div class="check-label">Daily Newsletter</div>
  <div class="subscribe"><i><svg width="8" height="8" viewBox="0 0 10 10"><path d="M2 5l2 2 4-4.5" stroke="#e8313f" fill="none" stroke-width="2"/></svg></i>Subscribe</div>
</div>
<div class="abs mail-badge">
  <svg width="34" height="26" viewBox="0 0 34 26"><rect x="1" y="1" width="32" height="24" fill="none" stroke="#fff" stroke-width="2"/><path d="M1 1l16 13L33 1M1 25l12-12M33 25L21 13" fill="none" stroke="#fff" stroke-width="2"/></svg>
</div>
<div class="abs decline">No Thank You, I want to pay full price</div>
</body>
</html>
```